Stonebrace Business Card Design

The Stonebrace Co is an aggregate (crushing) equipment dealer serving Western Canadian provinces. Stonebrace is a distributor of aggregate equipment for different manufacturers.

We are looking to change and update the existing business card which has been used since the existence of the company. A copy of existing card has been attached for reference. The Stonebrace Co logo we want to remain the same and we want the green color to remain the same.

We are wanting something new with a different look. A refreshing card to show a new modern and updated look. No longer wanting to have the manufacturers on the back of the card but something more like our logo on the back of the card with a statement like "Crushing Solutions"

ideas could be:
- card can be different colors on front and back
- front or reverse of the card could possibly be the green color with the logo in black

Target Market(s)

Owners of Aggregate/Crushing companies

Contact Information for Business Card

see above

Requirements
Must have
• - logo to remain same along with same font within logo
• - green color to remain same
Nice to have
• as noted above under project description
Should not have

```html
<!DOCTYPE html>
<html lang="en">
<head>
<meta charset="utf-8">
<title>The Stonebrace Co – Business Card</title>
<link rel="stylesheet" href="https://fonts.googleapis.com/css2?family=Roboto+Condensed:ital,wght@0,400;0,700;1,400&display=swap">
<style>
  :root {
    --brand-green: #8a9107;
    --charcoal: #2a2829;
    --paper: #f7f7f5;
    --ink: #231f20;
    --backdrop: #e9e6e0;
    --white: #ffffff;
  }
  * { box-sizing: border-box; margin: 0; padding: 0; }
  html, body { width: 1200px; height: 911px; overflow: hidden; }
  body {
    background: var(--backdrop);
    font-family: "Roboto Condensed", "Arial Narrow", sans-serif;
    position: relative;
  }
  .card {
    position: absolute;
    width: 525px;
    height: 300px;
    border-radius: 18px;
    overflow: hidden;
    box-shadow: 0 10px 28px rgba(0,0,0,.22);
  }
  .card--front { left: 50px; top: 306px; background: var(--paper); }
  .card--back  { left: 625px; top: 306px; background: var(--brand-green); }

  .front-shape { position: absolute; inset: 0; }

  .brand {
    position: absolute;
    display: flex;
    align-items: center;
    gap: 12px;
    font-weight: 700;
    text-transform: uppercase;
    letter-spacing: .3px;
    white-space: nowrap;
  }
  .brand__dot { border-radius: 50%; flex: none; }
  .card--front .brand {
    left: 32px; top: 38px;
    flex-direction: column;
    align-items: center;
    gap: 10px;
    font-size: 19px;
    color: var(--ink);
  }
  .card--front .brand__dot { width: 44px; height: 44px; background: var(--brand-green); }

  .contact {
    position: absolute;
    left: 268px;
    top: 108px;
    color: var(--white);
  }
  .contact__name {
    font-size: 24px;
    font-weight: 400;
    text-transform: uppercase;
    color: var(--brand-green);
    line-height: 1;
  }
  .contact__title {
    font-size: 15px;
    text-transform: uppercase;
    margin-top: 4px;
    margin-bottom: 16px;
  }
  .contact__line { font-size: 12.5px; line-height: 1.6; white-space: nowrap; }

  .card--back .brand {
    left: 50%; top: 110px; transform: translateX(-50%);
    font-size: 30px; color: var(--ink);
  }
  .card--back .brand__dot { width: 52px; height: 52px; background: var(--ink); }
  .tagline {
    position: absolute;
    left: 40px; bottom: 34px;
    font-size: 16px;
    font-style: italic;
    color: var(--ink);
  }
</style>
</head>
<body>
  <section class="card card--front" aria-label="Card front">
    <svg class="front-shape" width="525" height="300" viewBox="0 0 525 300" aria-hidden="true">
      <path d="M300 0 Q250 200 0 300 L525 300 L525 0 Z" fill="var(--charcoal)"/>
      <path d="M292 0 Q242 196 -8 296" fill="none" stroke="var(--brand-green)" stroke-width="4"/>
    </svg>
    <div class="brand"><span class="brand__dot"></span><span class="brand__name">The Stonebrace Co.</span></div>
    <div class="contact">
      <p class="contact__name">Dale Marsten</p>
      <p class="contact__title">CEO/Founder</p>
      <p class="contact__line">2210- 48B Avenue, Camrose, Alberta T4V 1K8</p>
      <p class="contact__line">P. 780.555.0142 M. 780.555.0187 F. 780.555.0163</p>
      <p class="contact__line">E. dale@stonebrace.com W. www.stonebrace.ca</p>
    </div>
  </section>

  <section class="card card--back" aria-label="Card back">
    <div class="brand"><span class="brand__dot"></span><span class="brand__name">The Stonebrace Co.</span></div>
    <p class="tagline">Crushing Solutions</p>
  </section>
</body>
</html>
```